Business Card for a mobile physiotherapy company

I need a layout for a business card for a mobile physiotherapy company.
Slogan is "Mobile Physiotherapy - Your Road To Recovery"
Phone number is 867-555-0142
Email VardenTherapy@postnest.ca (subject to change with website)
Website www.VardenTherapy.ca
My name and credentials: Luke Varden Luke Varden, BSc(kin), MPT, CAFCI, IMS
Information maybe included: Direct Billing, Services including Physiotherapy, IMS, acupuncture
Maybe include facebook and instagram logos
One side with the logo clean and sharp
Other side with details, try not to look too busy, keep everything concise

```html
<!DOCTYPE html>
<html lang="en">
<head>
<meta charset="utf-8">
<title>Varden Therapy – Business Card</title>
<link rel="stylesheet" href="https://fonts.googleapis.com/css2?family=Mulish:wght@700&family=Questrial&display=swap">
<style>
  :root {
    --navy: #274067;
    --stage: #dcdcdc;
    --card-light: #e6e6e6;
    --text-grey: #5f5f5f;
    --rule-grey: #8a8a8a;
    --white: #f4f4f4;
  }
  * { margin: 0; padding: 0; box-sizing: border-box; }
  html, body { width: 1200px; height: 1200px; overflow: hidden; }
  body {
    background: var(--stage);
    position: relative;
    font-family: "Questrial", "Century Gothic", sans-serif;
  }
  .card {
    position: absolute;
    left: 227px;
    width: 746px;
    height: 425px;
  }
  .card--front { top: 135px; background: var(--card-light); }
  .card--back  { top: 640px; background: var(--navy); }

  .wordmark {
    position: absolute;
    left: 0; right: 0;
    text-align: center;
    font-family: "Questrial", "Century Gothic", sans-serif;
    line-height: 1;
  }
  .wordmark__main { display: block; font-size: 56px; letter-spacing: 6px; }
  .wordmark__sub  { display: block; font-size: 22px; letter-spacing: 14px; margin-top: 12px; padding-left: 14px; }
  .card--front .wordmark { top: 92px; color: var(--navy); }
  .card--back .wordmark  { top: 160px; color: var(--white); }

  .holder {
    position: absolute;
    top: 233px; left: 0; right: 0;
    text-align: center;
  }
  .holder__name {
    font-family: "Mulish", "Century Gothic", sans-serif;
    font-weight: 700;
    font-size: 23px;
    color: var(--navy);
  }
  .holder__credentials {
    margin-top: 6px;
    font-size: 16px;
    color: var(--text-grey);
  }

  .divider {
    position: absolute;
    top: 304px; left: 0; right: 0;
    height: 1px;
    background: var(--rule-grey);
  }
  .divider__accent {
    position: absolute;
    top: -1px; left: 253px;
    width: 240px; height: 2px;
    background: var(--navy);
  }

  .contacts {
    position: absolute;
    top: 323px; left: 35px;
    list-style: none;
  }
  .contacts li, .services li {
    height: 24px;
    display: flex;
    align-items: center;
    font-size: 18px;
    color: var(--text-grey);
    white-space: nowrap;
  }
  .contacts svg { width: 19px; height: 19px; margin-right: 10px; flex: none; }

  .services {
    position: absolute;
    top: 323px; right: 35px;
    list-style: none;
    text-align: right;
  }
  .services li { justify-content: flex-end; }
  .services li::after {
    content: "";
    width: 7px; height: 7px;
    border-radius: 50%;
    background: var(--navy);
    margin-left: 8px;
  }

  .slogan {
    position: absolute;
    top: 300px; left: 0; right: 0;
    text-align: center;
    font-size: 18px;
    color: var(--white);
  }
  .social {
    position: absolute;
    top: 361px; left: 342px;
    display: flex;
    gap: 6px;
  }
  .social__dot {
    width: 28px; height: 28px;
    border-radius: 50%;
    background: var(--white);
  }
</style>
</head>
<body>

  <section class="card card--front">
    <div class="wordmark">
      <span class="wordmark__main">VARDEN</span>
      <span class="wordmark__sub">THERAPY</span>
    </div>

    <div class="holder">
      <p class="holder__name">Luke Varden Luke Varden</p>
      <p class="holder__credentials">BSc(kin), MPT, CAFCI, IMS</p>
    </div>

    <div class="divider"><span class="divider__accent"></span></div>

    <ul class="contacts">
      <li>
        <svg viewBox="0 0 20 20" aria-hidden="true">
          <circle cx="10" cy="10" r="10" fill="#274067"/>
          <path d="M6.5 5.5l2 0 .8 2.2-1.2 1a6 6 0 0 0 2.8 2.8l1-1.2 2.2.8v2c0 .6-.5 1-1 1A9 9 0 0 1 5.5 6.5c0-.5.4-1 1-1z" fill="#e6e6e6"/>
        </svg>
        867-555-0142
      </li>
      <li>
        <svg viewBox="0 0 20 20" aria-hidden="true">
          <circle cx="10" cy="10" r="10" fill="#274067"/>
          <rect x="5" y="6.5" width="10" height="7" fill="none" stroke="#e6e6e6" stroke-width="1.1"/>
          <path d="M5 6.5l5 4 5-4" fill="none" stroke="#e6e6e6" stroke-width="1.1"/>
        </svg>
        VardenTherapy@postnest.ca
      </li>
      <li>
        <svg viewBox="0 0 20 20" aria-hidden="true">
          <circle cx="10" cy="10" r="10" fill="#274067"/>
          <circle cx="10" cy="10" r="5.5" fill="none" stroke="#e6e6e6" stroke-width="1"/>
          <ellipse cx="10" cy="10" rx="2.3" ry="5.5" fill="none" stroke="#e6e6e6" stroke-width="1"/>
          <path d="M4.5 10h11M5.3 7.3h9.4M5.3 12.7h9.4" stroke="#e6e6e6" stroke-width="0.9"/>
        </svg>
        www.VardenTherapy.ca
      </li>
    </ul>

    <ul class="services">
      <li>Direct Billing</li>
      <li>Services including Physiotherapy</li>
      <li>IMS, acupuncture</li>
    </ul>
  </section>

  <section class="card card--back">
    <div class="wordmark">
      <span class="wordmark__main">VARDEN</span>
      <span class="wordmark__sub">THERAPY</span>
    </div>
    <p class="slogan">Mobile Physiotherapy - Your Road To Recovery</p>
    <div class="social" aria-label="Social media">
      <span class="social__dot"></span>
      <span class="social__dot"></span>
    </div>
  </section>

</body>
</html>
```